Varnik Holdings — Business Card Design Brief
Overview
Design a double-sided business card for Varnik Holdings that highlights our two service arms: Varnik Communications (telecommunications) and Varnik Energy (business energy solutions). The card should feel smart and stand out when handed to clients.

Objectives
Showcase our areas of specialty clearly.
Reflect the overall Varnik / Varnik Holdings brand while acknowledging both arms.
Explore using both logos (Communications + Energy) or one unified logo, depending on the design.

Deliverables
One double-sided business card design (front + back).

Content & Copy
Front (preferred): Logo: Varnik / Varnik Holdings
Descriptor: Business Communications | Business Energy
Back:My contact details and company details
Core products: Business Mobile • Telephony • Internet • Business Energy Solutions

Brand & Visual Direction
We have a group logo currently tailored more toward telecoms, plus a separate Varnik Energy logo.
Please explore layouts that use both logos or just one, whichever works best.
Color: I wouldn't mind seeing an option using our the Blue/Purple gradient from our website (varnik-example.co.uk), but also open to non-gradient approaches and other colours..

Overall look: Smart, modern, and distinctive.
Format & Print Specs
Double-sided business card format. (Use a standard size

Must-Haves
Front: Varnik wording or Varnik Holdings wording with atleast 1 logo also on front “Business Communications | Business Energy.”

Back: Contact + company details and core products.
A design that stands out while remaining professional.

Nice-to-Have Options
A gradient version using our site’s Blue/Purple gradient.
A non-gradient version.
A dual-logo treatment versus a single-logo treatment.

Thanks
Owen

```html
<!DOCTYPE html>
<html lang="en">
<head>
<meta charset="utf-8">
<title>Varnik Holdings — Business Card</title>
<link href="https://fonts.googleapis.com/css2?family=Poppins:wght@700&family=Arimo:wght@400&display=swap" rel="stylesheet">
<style>
  :root {
    --canvas: #e9e9e9;
    --paper: #ffffff;
    --navy: #1a1a6e;
    --blue: #0d62d8;
    --blue-light: #0a93dc;
    --green: #3aa312;
    --green-dark: #40aa10;
    --lime: #b5cc00;
    --ink: #444444;
    --rule: #c8c8c8;
  }
  * { margin: 0; padding: 0; box-sizing: border-box; }
  html, body { width: 1200px; height: 1200px; overflow: hidden; background: var(--canvas); }
  .card { position: absolute; width: 689px; height: 393px; overflow: hidden; box-shadow: 0 14px 26px rgba(0,0,0,.18); }
  .card-front { left: 267px; top: 159px; background: var(--paper); }
  .card-back { left: 262px; top: 654px; display: flex; }

  .brand { position: absolute; display: flex; flex-direction: column; }
  .brand-mark { width: 78px; height: 78px; border-radius: 50%; border: 9px solid var(--blue); }
  .brand-name { font-family: "Poppins", sans-serif; font-weight: 700; color: var(--navy); font-size: 42px; line-height: 1; letter-spacing: .5px; margin-top: 14px; }
  .brand-comms { left: 42px; top: 30px; align-items: flex-start; }
  .brand-energy { right: 46px; top: 30px; align-items: flex-end; }
  .brand-energy .brand-mark { border-color: var(--green); margin-right: 108px; }

  .person { position: absolute; left: 42px; top: 208px; }
  .person-name { font-family: "Poppins", sans-serif; font-weight: 700; color: var(--navy); font-size: 26px; line-height: 1.1; letter-spacing: .5px; }
  .person-role { font-family: "Arimo", sans-serif; color: var(--green); font-size: 16px; margin-top: 2px; }

  .divider { position: absolute; left: 42px; top: 265px; width: 615px; height: 1px; background: var(--rule); }

  .contact-list { position: absolute; left: 42px; top: 274px; list-style: none; font-family: "Arimo", sans-serif; font-size: 17px; color: var(--ink); }
  .contact-list li { display: flex; align-items: center; height: 20.5px; }
  .contact-list svg { width: 14px; height: 14px; margin-right: 9px; fill: var(--navy); }

  .address { position: absolute; right: 40px; top: 276px; text-align: right; font-family: "Arimo", sans-serif; font-size: 17px; line-height: 20.5px; color: var(--ink); font-style: normal; }

  .product-band { position: absolute; left: 0; bottom: 0; width: 100%; height: 35px; display: flex; font-family: "Arimo", sans-serif; font-size: 18px; color: #fff; }
  .product-band .comms { width: 417px; background: var(--blue); display: flex; align-items: center; padding-left: 41px; gap: 16px; border-right: 2px solid #fff; }
  .product-band .energy { flex: 1; background: var(--green); display: flex; align-items: center; padding-left: 18px; }

  .back-half { height: 100%; display: flex; flex-direction: column; align-items: center; color: #fff; }
  .back-comms { width: 352px; background: linear-gradient(90deg, var(--blue), var(--blue-light)); }
  .back-energy { flex: 1; background: linear-gradient(90deg, var(--green-dark), var(--lime)); }
  .back-mark { width: 100px; height: 100px; border-radius: 50%; border: 10px solid #fff; margin-top: 100px; }
  .back-name { font-family: "Poppins", sans-serif; font-weight: 700; font-size: 52px; line-height: 1; margin-top: 14px; letter-spacing: 1px; }
  .back-tag { font-family: "Arimo", sans-serif; font-size: 17px; margin-top: 26px; }
  .back-energy .back-tag { letter-spacing: 3px; }
</style>
</head>
<body>
  <section class="card card-front">
    <div class="brand brand-comms">
      <span class="brand-mark"></span>
      <span class="brand-name">VARNIK</span>
    </div>
    <div class="brand brand-energy">
      <span class="brand-mark"></span>
      <span class="brand-name">VARNIK</span>
    </div>

    <div class="person">
      <div class="person-name">DANIEL MARSH</div>
      <div class="person-role">President</div>
    </div>

    <div class="divider"></div>

    <ul class="contact-list">
      <li><svg viewBox="0 0 16 16"><path d="M3.5 1l3 3-1.5 2c1 2 3 4 5 5l2-1.5 3 3-2 2C7 14 2 9 1.5 3z"/></svg>555-214-7830</li>
      <li><svg viewBox="0 0 16 16"><path d="M4 0h8a1 1 0 011 1v14a1 1 0 01-1 1H4a1 1 0 01-1-1V1a1 1 0 011-1zm1 2v10h6V2z"/></svg>555-219-4471</li>
      <li><svg viewBox="0 0 16 16"><path d="M0 3h16v10H0zm2 2v.5l6 4 6-4V5l-6 4z"/></svg>info@varnik-example.com</li>
    </ul>

    <address class="address">
      214 Larkfield Road<br>
      Brampton, Canada 512<br>
      www.varnik-example.com
    </address>

    <div class="product-band">
      <div class="comms"><span>Business Mobile</span><span>•</span><span>Telephony</span><span>•</span><span>Internet</span></div>
      <div class="energy">Business Energy Solutions</div>
    </div>
  </section>

  <section class="card card-back">
    <div class="back-half back-comms">
      <span class="back-mark"></span>
      <span class="back-name">VARNIK</span>
      <span class="back-tag">BUSINESS COMMUNICATIONS</span>
    </div>
    <div class="back-half back-energy">
      <span class="back-mark"></span>
      <span class="back-name">VARNIK</span>
      <span class="back-tag">BUSINESS ENERGY</span>
    </div>
  </section>
</body>
</html>
```